International Career Development Workshop

I need a Powerpoint revised and designed in a more professional manner for a presentation I will be giving. We are an International Education Company that provides students with Internships Abroad, and are expanding our career development programming to offer more guidance through on-site workshops. I am happy to send along our website to showcase the colors and fonts we use, but we tend to use royal blue, lime green, and white in our color scheme. The final design should communicate opportunity and self-awareness within college students.

Target Market(s)

College Students, University Partners, and International Education Community

Industry/Entity Type

Education

Font styles to use
Sans Serif

Colors
9bcb3b
0355a3
ffffff

Requirements
Must have
• Our logo, our color scheme, a unified, professional theme throughout, Watermark of our logo, thematic sections spread across four sections.
Nice to have
• Videos and graphics
Should not have
• Spelling Errors, sloppy design

```html
<!DOCTYPE html>
<html lang="en">
<head>
<meta charset="utf-8">
<title>Project Title Here</title>
<link rel="stylesheet" href="https://fonts.googleapis.com/css2?family=Lato:wght@400;700;900&display=swap">
<style>
  :root {
    --royal-blue: #0355a3;
    --header-blue: #0b4f98;
    --lime: #9bcb3b;
    --lime-band: #a8d400;
    --white: #ffffff;
    --body-grey: #6a6a6a;
    --watermark: #f1f4f9;
  }
  * { margin: 0; padding: 0; box-sizing: border-box; }
  html, body {
    width: 1200px;
    height: 900px;
    overflow: hidden;
    background: var(--white);
  }
  .slide {
    position: relative;
    width: 1200px;
    height: 900px;
    background: var(--white);
    font-family: 'Lato', Arial, sans-serif;
    overflow: hidden;
  }
  .header-bar {
    position: absolute;
    top: 0; left: 0;
    width: 1200px;
    height: 85px;
    background: var(--header-blue);
  }
  .slide-title {
    position: absolute;
    left: 33px;
    top: 20px;
    color: var(--white);
    font-weight: 900;
    font-size: 39px;
    letter-spacing: 0.3px;
  }
  .brand {
    position: absolute;
    right: 32px;
    top: 22px;
    display: flex;
    align-items: center;
    gap: 12px;
  }
  .brand-dot {
    width: 36px;
    height: 36px;
    border-radius: 50%;
    background: var(--white);
  }
  .brand-name {
    color: var(--white);
    font-weight: 700;
    font-size: 24px;
    letter-spacing: 0.5px;
  }
  .watermark {
    position: absolute;
    left: 390px;
    top: 250px;
    width: 420px;
    height: 420px;
    border-radius: 50%;
    background: var(--watermark);
  }
  .section {
    position: absolute;
    left: 30px;
    width: 1130px;
  }
  .section-marker {
    position: absolute;
    left: 0;
    top: 6px;
    width: 46px;
    height: 46px;
    border-radius: 50%;
    background: var(--royal-blue);
  }
  .section-title {
    position: absolute;
    left: 70px;
    top: 0;
    color: var(--royal-blue);
    font-weight: 700;
    font-size: 31px;
    line-height: 40px;
  }
  .section-body {
    position: absolute;
    left: 70px;
    top: 42px;
    width: 1052px;
    color: var(--body-grey);
    font-size: 22px;
    line-height: 39px;
  }
  .section-body .line {
    display: block;
    text-align: justify;
    text-align-last: justify;
    white-space: nowrap;
  }
  .section-body .line.last {
    text-align-last: left;
  }
  .section-one { top: 150px; }
  .section-two { top: 376px; }
  .section-three { top: 588px; }
  .footer-bar {
    position: absolute;
    left: 0;
    top: 860px;
    width: 1200px;
    height: 40px;
    background: var(--lime-band);
  }
  .copyright {
    position: absolute;
    left: 30px;
    top: 6px;
    color: var(--white);
    font-size: 22px;
  }
  .page-number {
    position: absolute;
    left: 1136px;
    top: 845px;
    width: 46px;
    height: 46px;
    border-radius: 50%;
    background: var(--white);
    border: 3px solid var(--lime-band);
    color: var(--royal-blue);
    font-weight: 900;
    font-size: 20px;
    display: flex;
    align-items: center;
    justify-content: center;
  }
</style>
</head>
<body>
<main class="slide">
  <header class="header-bar">
    <h1 class="slide-title">PROJECT TITLE HERE</h1>
    <div class="brand">
      <span class="brand-dot"></span>
      <span class="brand-name">Horizon Abroad</span>
    </div>
  </header>

  <div class="watermark" aria-hidden="true"></div>

  <section class="section section-one">
    <span class="section-marker"></span>
    <h2 class="section-title">Subtitle Here</h2>
    <p class="section-body">
      <span class="line">chocolate chocolate cake carrot cake dragée candy canes gummies bear cake icing oat cake jelly choc-</span>
      <span class="line">olate chocolate cake carrot cake dragée candy canes gummies bear Gummies cake icing oat cake jelly</span>
      <span class="line last">chocolate chocolate cake carrot cake dragée candy canes</span>
    </p>
  </section>

  <section class="section section-two">
    <span class="section-marker"></span>
    <h2 class="section-title">Subtitle Here</h2>
    <p class="section-body">
      <span class="line">chocolate chocolate cake carrot cake dragée candy canes gummies bear cake icing oat cake jelly choc-</span>
      <span class="line">olate chocolate cake carrot cake dragée candy canes gummies bear Gummies cake icing oat cake jelly</span>
      <span class="line last">chocolate chocolate cake carrot cake dragée candy canes</span>
    </p>
  </section>

  <section class="section section-three">
    <span class="section-marker"></span>
    <h2 class="section-title">Subtitle Here</h2>
    <p class="section-body">
      <span class="line">chocolate chocolate cake carrot cake dragée candy canes gummies bear cake icing oat cake jelly choc-</span>
      <span class="line">olate chocolate cake carrot cake dragée candy canes gummies bear Gummies cake icing oat cake jelly</span>
      <span class="line last">chocolate chocolate cake carrot cake dragée candy canes</span>
    </p>
  </section>

  <footer class="footer-bar">
    <p class="copyright">Copyright text here</p>
  </footer>
  <div class="page-number">01</div>
</main>
</body>
</html>
```